Computer Consulting Brochure

Computer Consulting services for schools, small businesses, local governments and medical offices. We design networks, security, monitoring, applications for these environments.
Updates
Project Deadline Extended Reason: I provided a condensed document so as not to overwhelm designers. This document covers only pertinent info that can be further condensed if necessary for physical size constraints. Added Friday, April 7, 2017
Target Market(s)
Schools, Small Businesses, Medical Offices, Local Governments. 4 brochures that are identical except for a section that specifically describes the 4 markets.
Industry/Entity Type
Computer
Colors
Designer to choose colors to be used in the design.
Look and feel
Each slider illustrates characteristics of the customer's brand and the style your logo design should communicate.

```html
<!DOCTYPE html>
<html lang="en">
<head>
<meta charset="utf-8">
<title>BrightLine IT – Tri-fold Brochure</title>
<link rel="stylesheet" href="https://fonts.googleapis.com/css2?family=Barlow:wght@300;400;500&family=Barlow+Condensed:wght@400;500;600&display=swap">
<style>
:root{
  --blue:#1e9ac6;
  --blue-dark:#1683b0;
  --blue-light:#6ec6e3;
  --yellow:#f6b828;
  --orange:#ee9a1c;
  --cream:#fdf3d6;
  --ink:#3a3a3a;
  --white:#ffffff;
  --bg:#e9e6e1;
}
*{margin:0;padding:0;box-sizing:border-box}
html,body{width:1200px;height:1200px;overflow:hidden;background:var(--bg)}
body{position:relative;font-family:"Barlow",Arial,sans-serif;color:var(--ink)}
.spread{position:absolute;left:210px;width:780px;height:590px;background:var(--white);box-shadow:0 2px 8px rgba(0,0,0,.15);overflow:hidden}
.spread--outside{top:6px;display:flex}
.spread--inside{top:604px}
.panel{position:relative;width:260px;height:590px;overflow:hidden}
.panel-title{font-family:"Barlow Condensed",Arial,sans-serif;font-weight:600;color:var(--blue);font-size:21px;line-height:1;text-transform:uppercase;margin-bottom:6px}
.body p{font-size:9.3px;font-weight:300;line-height:1.32;margin-bottom:7px}
.body .lead{font-family:"Barlow Condensed",Arial,sans-serif;font-weight:600;color:var(--blue);font-size:12.5px;line-height:1.15;margin-bottom:8px}
.pad{position:absolute;left:14px;right:12px;top:14px;z-index:1}
.photo{position:absolute}
/* outside left */
.desk-photo{left:0;right:0;bottom:0;height:230px;background:linear-gradient(180deg,rgba(255,255,255,1) 0%,rgba(226,214,196,.7) 35%,#b9a486 100%)}
.projects{list-style:none}
.projects li{position:relative;padding-left:10px;font-size:8.6px;font-weight:300;line-height:1.25;margin-bottom:4px}
.projects li::before{content:"";position:absolute;left:0;top:3px;width:6px;height:6px;background:var(--blue-light)}
.solutions{position:absolute;left:0;right:0;top:275px;bottom:0;background:linear-gradient(180deg,var(--blue-light) 0%,var(--blue) 100%);color:var(--white);padding:24px 10px 0}
.solutions h3{font-family:"Barlow Condensed",Arial,sans-serif;font-weight:500;font-size:15.5px;line-height:1.22;text-align:center;text-transform:uppercase;color:#fff8e1}
.contact{list-style:none;position:absolute;left:22px;bottom:10px}
.contact li{display:flex;align-items:center;gap:8px;font-family:"Barlow Condensed",Arial,sans-serif;font-size:11px;font-weight:500;margin-top:4px}
.contact svg{width:11px;height:11px;flex:none}
/* cover */
.cover-photo{left:0;right:0;top:0;height:275px;background:linear-gradient(135deg,#f2e6d6 0%,#e4b57a 40%,#9aa2ae 75%,#4e5663 100%)}
.brand{position:absolute;top:14px;right:16px;font-family:"Barlow",Arial,sans-serif;font-weight:400;font-size:17px;color:var(--blue-dark)}
.cover-band{position:absolute;left:0;right:0;top:275px;bottom:0;background:linear-gradient(180deg,var(--yellow) 0%,var(--orange) 100%);padding:20px 14px 0}
.cover-title{font-family:"Barlow Condensed",Arial,sans-serif;font-weight:400;color:var(--white);font-size:46px;line-height:.92;text-transform:uppercase;padding-bottom:4px;border-bottom:2px solid var(--white)}
.cover-sub{font-family:"Barlow Condensed",Arial,sans-serif;color:var(--blue-dark);font-size:21px;line-height:1.05;margin-top:8px}
.cover-sub b{font-weight:600;text-transform:uppercase}
.cover-list{display:grid;grid-template-columns:52px 1fr;margin-top:10px;color:var(--white)}
.cover-list .for{font-family:"Barlow Condensed",Arial,sans-serif;font-size:20px;line-height:1}
.cover-list h4{font-family:"Barlow Condensed",Arial,sans-serif;font-weight:600;color:var(--blue-dark);font-size:15px;line-height:1;text-transform:uppercase}
.cover-list p{font-family:"Barlow Condensed",Arial,sans-serif;font-size:10px;line-height:1.1;text-transform:uppercase;margin:3px 0 10px}
/* inside */
.layer{position:absolute;top:0;bottom:0}
.bg-left{left:0;width:260px;background:linear-gradient(180deg,#d7eff8 0%,#eef8fb 45%)}
.bg-right{left:520px;width:260px;background:linear-gradient(180deg,var(--cream) 0%,#fbe7ad 100%)}
.relax-photo{left:0;width:520px;bottom:0;height:290px;background:linear-gradient(180deg,rgba(255,255,255,0) 0%,#c9ced2 30%,#9aa5ad 70%,#7c858a 100%)}
.band{position:absolute;top:0;height:88px;display:flex;align-items:center}
.band--blue{left:0;width:520px;background:linear-gradient(90deg,var(--blue-light),#8fd3ea);padding-left:20px}
.band--blue h2{font-family:"Barlow Condensed",Arial,sans-serif;font-weight:600;font-size:38px;color:var(--white);text-transform:uppercase}
.band--yellow{left:520px;width:260px;background:var(--yellow);padding-left:16px}
.band--yellow h2{font-family:"Barlow Condensed",Arial,sans-serif;font-weight:500;font-size:18px;line-height:1.05;color:var(--white);text-transform:uppercase}
.inside-panels{position:absolute;inset:0;display:flex}
.col{position:absolute;top:105px;left:16px;right:14px}
.sub-yellow{font-family:"Barlow Condensed",Arial,sans-serif;font-weight:600;color:var(--orange);font-size:12px;line-height:1.12;margin-bottom:6px}
.checklist{list-style:none}
.checklist li{position:relative;padding-left:10px;font-size:9px;font-weight:300;line-height:1.25;margin-bottom:7px}
.checklist li::before{content:"";position:absolute;left:0;top:3px;width:6px;height:6px;background:var(--orange)}
</style>
</head>
<body>

<section class="spread spread--outside" aria-label="Brochure outside">
  <article class="panel">
    <div class="photo desk-photo" role="img" aria-label="Photo of a desk from above with a keyboard, mouse, coffee cup and hands typing"></div>
    <div class="pad body">
      <h2 class="panel-title">Small Businesses</h2>
      <p class="lead">Small businesses must concentrate their time and energy on knowing their own industry – and that often means that effective technology practices get overlooked.</p>
      <p>Small businesses often don't have the resources or inclination to track the latest computer news, security threats, or even common break/fix tips. And not all small business owners are adept at maintaining best technology practices.</p>
      <p>Small businesses need knowledgeable, trusted technology partners who are proficient with current technologies and willing to help learn their industry's operations requirements. Once a qualified technology expert is familiar with a client's needs, appropriate services and solutions can be recommended and deployed. This partnership produces cost effective, efficient and more profitable solutions for your business.</p>
      <p>We achieve this effect by ensuring that all network components are integrated and provide appropriate access points for data input and network traffic is intelligently routed based upon parameters set by you (e.g. user id, type of device identifier, or intelligent routing by type of data). Physical components should be the proper mix of Ethernet, fiber, advanced wireless and others which are selected based upon your requirements, size of environment, and types of physical structures. Also blended into the communication environment are appropriate safeguards that ensure the communication capabilities are kept safe and secure and only intended uses are permitted and intrusions are detected and stopped.</p>
    </div>
  </article>

  <article class="panel">
    <div class="pad">
      <h2 class="panel-title">Some Recent Projects</h2>
      <ul class="projects">
        <li>Resolved a major problem at NSU for one of their computer clusters used in their research department.</li>
        <li>Participated in a twenty million dollar project for Westmark County to upgrade all school environments to provide connectivity for every student on high speed wireless (1:1 computing).</li>
        <li>Created a Larix implementation in a large commercial environment. Designed a Larix mail server running on the Nimbus cloud for hundreds of users.</li>
        <li>Provided 24x7 monitoring and support for a large boarding school. Designed and installed a wireless LAN that covered a large campus and also integrated a security camera system. Created a mobile device management system for student Slate tablets, providing appropriate student permissions.</li>
        <li>Created a Keystone Directory domain and related security for a newly constructed medical office. Connected an ultrasound machine to the IT network and enabled external authorized doctors to securely connect to the server to view ultrasound recordings.</li>
      </ul>
    </div>
    <div class="solutions">
      <h3>Our solutions for schools, medical/dental, small businesses and auto dealerships are cost effective because they are customized specifically for your environment. Your type of business and end users are critical factors that should be the influencing design parameters</h3>
      <ul class="contact">
        <li><svg viewBox="0 0 12 12"><circle cx="6" cy="6" r="6" fill="#fff"/><rect x="3" y="3.5" width="6" height="4" fill="none" stroke="#1e9ac6" stroke-width="1"/><rect x="5" y="7.5" width="2" height="1.5" fill="#1e9ac6"/></svg>www.BrightLineIT.com</li>
        <li><svg viewBox="0 0 12 12"><circle cx="6" cy="6" r="6" fill="#fff"/><rect x="3" y="4" width="6" height="4.2" fill="none" stroke="#1e9ac6" stroke-width="1"/><path d="M3 4l3 2.4L9 4" fill="none" stroke="#1e9ac6" stroke-width="1"/></svg>info@BrightLineIT.com</li>
        <li><svg viewBox="0 0 12 12"><circle cx="6" cy="6" r="6" fill="#fff"/><path d="M4 3c-1 1-1 2.5 1 4.5S8 10 9 9l-1.2-1.3-1 .6C6 7.8 4.8 6.6 4.4 5.7l.6-1z" fill="#1e9ac6"/></svg>401-555-0142</li>
        <li><svg viewBox="0 0 12 12"><circle cx="6" cy="6" r="6" fill="#fff"/><path d="M6 2.5a2.3 2.3 0 0 0-2.3 2.3C3.7 6.7 6 9.5 6 9.5s2.3-2.8 2.3-4.7A2.3 2.3 0 0 0 6 2.5z" fill="#1e9ac6"/><circle cx="6" cy="4.8" r=".9" fill="#fff"/></svg>18 Elm St #210 Millbrook, RI 02800-0210</li>
      </ul>
    </div>
  </article>

  <article class="panel">
    <div class="photo cover-photo" role="img" aria-label="Photo of colleagues reviewing charts on a laptop in warm sunlight"></div>
    <div class="brand">BrightLine IT</div>
    <div class="cover-band">
      <h1 class="cover-title">We do everything</h1>
      <p class="cover-sub"><b>Design, Install, Modify</b><br>and <b>Monitor(24x7)</b></p>
      <div class="cover-list">
        <span class="for">for</span>
        <div>
          <h4>IT Environments</h4>
          <p>Each environment is customized for either schools, medical/ dental, small businesses or auto dealerships</p>
          <h4>Security Camera<br>Monitoring Systems</h4>
          <p>HD, digital and economically integrated into the IT environment</p>
        </div>
      </div>
    </div>
  </article>
</section>

<section class="spread spread--inside" aria-label="Brochure inside">
  <div class="layer bg-left"></div>
  <div class="layer bg-right"></div>
  <div class="photo relax-photo" role="img" aria-label="Photo of a relaxed man leaning back at his desk with a laptop and a plant"></div>
  <div class="band band--blue"><h2>Why outsource?</h2></div>
  <div class="band band--yellow"><h2>What we do<br>for all types of IT<br>environments</h2></div>

  <div class="inside-panels">
    <article class="panel">
      <div class="col body">
        <p class="lead">We specialize in IT support at a scale tailored to your exact requirements</p>
        <p>A direct, dedicated IT staff will have either idle time during periods of stability or inadequate resources for those times when problems occur simultaneously.</p>
        <p>By outsourcing to BrightLine IT your business will always have the ideal level of support, and therefore never overpay nor be insufficiently prepared to deal with sudden problems that can overwhelm insufficient numbers of staff.</p>
        <p>Because funds are allocated efficiently your business can now afford to capitalize on the most current technology and benefit from all features offered by these newest features.</p>
      </div>
    </article>

    <article class="panel">
      <div class="col body">
        <p>Outsourcing is the better economical choice; there are no overtime hours, paid vacations, morale problems, costs associated with health care and mandatory reporting, and other overhead expenses associated with employees.</p>
        <p>But cost is not the only reason to outsource. Your core business is not IT; therefore outsourcing eliminates the need for your personnel to be proficient in multiple areas, i.e. building specialized skills to support your core businesses and functions as well as accumulating skills enabling them to manage, enhance and maintain the ideal IT environment.</p>
        <p>The elimination of this responsibility allows you to focus on finding and developing personnel skills directly related to your business, and not compromising your core business components.</p>
      </div>
    </article>

    <article class="panel">
      <div class="col body">
        <h3 class="sub-yellow">Install, customize and support all elements of IT environments</h3>
        <p>We analyze your unique business requirements, determining if modifications are cost justified for your existing computing environment.</p>
        <h3 class="sub-yellow">Design the best combination of hardware and software for your environment</h3>
        <p>We specialize in Northwind, Corvane, Larix, Orchard, tablets and smart phones. We are able to structure each solution to the specific type of business to achieve the best returns on investment.</p>
        <h3 class="sub-yellow">Tailor all components of the entire IT environment</h3>
        <p>Install, customize, monitor</p>
        <ul class="checklist">
          <li>desktops</li>
          <li>multiple operating systems (Fenestra, Orchard, Larix, Unyx)</li>
          <li>Slate tablets</li>
          <li>network backbones and their components (Ethernet, fiber, routers, switches, advanced wireless)</li>
          <li>servers</li>
          <li>virtualization (thin clients/zero clients)</li>
          <li>firewalls</li>
          <li>virus/intruder detection</li>
          <li>data encryption</li>
          <li>data analysis and more</li>
        </ul>
      </div>
    </article>
  </div>
</section>

</body>
</html>
```